Premium Wraparound Label Design for 6 oz Plumberry Spread Jar – Keoni Bay Sweetworks

Design a continuous wraparound label for an 6 oz circular glass jar that integrates the Keoni Bay Sweetworks logo (featuring the pink and brown leaf motif) and the Plumberry Spread nutrition label into one cohesive, premium presentation. The design should feel authentically Hawaiian, classic, and handcrafted—reflecting the brand’s legacy of island-inspired desserts.
Label Specifications
Container: 8 oz round glass jar
Label Type: Full wraparound (one continuous label)
Approximate Label Size: 2.5 inches tall × 8.5 inches wide
Finish: Matte or satin with optional gold foil highlights
Print: CMYK-ready artwork with bleed and safe zones clearly marked
Design Elements to Integrate
1. Front Panel (Main Display Area):
Prominently feature the Keoni Bay Sweetworks logo centered and scaled proportionally.
Display the product name “Plumberry Spread” in elegant, legible typography that complements the logo.
Add the following text beneath or near the product name:
“Made in Hawai‘i”
“Net Wt. 8 oz (227g)”
“Keep Refrigerated” (in smaller but clear type).
Background tones should complement the logo—cream, soft tan, or pastel pink for warmth and harmony.
The front should communicate island sophistication—premium yet inviting.
2. Side Panel (Transition Area):
Create a smooth visual transition around the jar using a subtle, continuous background pattern such as tropical leaves, ocean wave textures, or gold accent lines.
Include the brand story text:
“Keoni Bay Sweetworks brings authentic island flavors to every table. Our signature Plumberry Spread blends tropical fruit and fresh cream for a taste of pure aloha.”
3. Back Panel (Informational Area):
Integrate the Plumberry Spread nutrition facts panel and ingredients list (from the attached file).
Ensure layout is FDA-compliant, legible, and well-balanced.
Beneath the ingredients, include:
“Manufactured by Keoni Bay Sweetworks, Hawai‘i.”
“Keep Refrigerated.”
Leave space for:
A QR code linking to the brand website and social media.
A barcode area, placed neatly near the bottom or corner.
Aesthetic Direction
Style: Premium, classic, and island-inspired
Color Palette: Cream base with warm browns, muted pinks, and gold accents
Typography:
Serif or script for product name and logo (for a classic, handcrafted look)
Clean sans-serif for informational text
Mood: Heritage meets handcrafted luxury — nostalgic yet refined
Finish Options:
Matte for artisanal authenticity
Satin or metallic foil for a modern, premium touch
Deliverables
Designers should submit:
3 design variations (e.g., classic heritage, minimalist modern, and premium tropical).
Editable source files (AI, PSD, or layered PDF) with bleed and safe zones clearly marked.
Mockups on an 8 oz round glass jar for visual presentation.

Target Market(s)

Craft fair consumers / tourist in hawaii

Industry/Entity Type

food and Bev

Logo Text

see description

Font styles to use
Serif
Sans Serif
Script

Requirements
Must have
• see description
Nice to have
• see description
Should not have
• see description

```html
<!DOCTYPE html>
<html lang="en">
<head>
<meta charset="utf-8">
<title>Keoni Bay Sweetworks – Plumberry Spread Label</title>
<link rel="stylesheet" href="https://fonts.googleapis.com/css2?family=Arimo:wght@400;700&family=Roboto+Condensed:wght@300;400&family=Josefin+Sans:wght@400;600&family=Saira+Condensed:wght@300;400&display=swap">
<style>
:root{
  --page:#e4e4e4;
  --brown:#522e10;
  --brown-text:#4a2a10;
  --cream:#e8dccf;
  --pink:#d98f91;
  --gold-dark:#b8860b;
  --gold-light:#f6dc7a;
  --white:#ffffff;
  --ink:#1e1a1a;
}
*{box-sizing:border-box;margin:0;padding:0}
html,body{width:1200px;height:1200px;overflow:hidden;background:var(--page)}
.label{position:absolute;left:72px;top:439px;width:1062px;height:313px;background:var(--brown);box-shadow:-6px 8px 10px rgba(0,0,0,.35)}
.gold-band{position:absolute;left:0;width:100%;height:7px;background:linear-gradient(90deg,var(--gold-dark),var(--gold-light) 20%,var(--gold-dark) 40%,var(--gold-light) 60%,var(--gold-dark) 80%,var(--gold-light))}
.gold-band.top{top:0}.gold-band.bottom{bottom:0}
.panel{position:absolute;top:7px;bottom:7px}
.panel.back{left:0;width:371px}
.panel.front{left:371px;width:388px;background:var(--cream)}
.panel.side{left:759px;width:303px}
.leaf-texture{position:absolute;inset:0;background:radial-gradient(ellipse 40% 45% at 60% 45%,rgba(140,80,40,.25),transparent 70%)}
.nutrition{position:absolute;left:30px;top:14px;width:130px;height:272px;border:1px solid #6b4a3a;background:linear-gradient(135deg,#c88d8b,#f6d6d8 45%,#fbe3e5 60%,#d9a3a2);padding:3px 4px;font-family:Arimo,sans-serif;color:var(--ink);font-size:5.6px;line-height:1.15}
.nutrition h3{font-size:17px;font-weight:700;line-height:1}
.nutrition .rule-thick{height:5px;background:var(--ink);margin:3px 0 4px}
.nutrition .rule-mid{height:2px;background:var(--ink);margin:2px 0}
.nutrition .row{border-bottom:.6px solid var(--ink);padding:1.6px 0 1.6px 0}
.nutrition .indent{padding-left:8px}
.nutrition .cal{display:flex;justify-content:space-between;font-size:13px;font-weight:700;line-height:1}
.nutrition .dv{text-align:right;font-weight:700;font-size:5px}
.nutrition .ingredients{margin-top:3px;font-size:6.2px;line-height:1.3}
.back-text{position:absolute;left:170px;width:195px;text-align:center;font-family:"Roboto Condensed",sans-serif;color:var(--white);font-size:11.5px;line-height:1.35}
.barcode-space{position:absolute;left:203px;top:247px;width:123px;height:30px;background:var(--white)}
.brand-mark{position:absolute;left:170px;top:30px;width:48px;height:48px;border-radius:50%;background:var(--pink)}
.brand-name{position:absolute;left:0;right:0;top:96px;text-align:center;font-family:"Josefin Sans",sans-serif;font-weight:600;color:var(--brown-text);font-size:26px;letter-spacing:1.5px;text-transform:uppercase;line-height:1.15}
.est{position:absolute;left:0;right:0;top:191px;display:flex;justify-content:center;align-items:center;gap:8px;font-family:"Josefin Sans",sans-serif;font-weight:600;font-size:9.5px;letter-spacing:1px;color:var(--brown-text)}
.est span.line{width:22px;height:1px;background:var(--brown-text)}
.product-name{position:absolute;left:0;right:0;top:208px;text-align:center;font-family:"Saira Condensed",sans-serif;font-weight:300;color:var(--pink);font-size:48px;letter-spacing:.5px;line-height:1}
.front-foot{position:absolute;top:283px;font-family:"Roboto Condensed",sans-serif;font-size:10.5px;color:var(--brown-text)}
.front-foot.net{left:47px}.front-foot.origin{right:51px}
.story{position:absolute;left:39px;top:37px;width:230px;font-family:"Roboto Condensed",sans-serif;color:var(--white);font-size:11.4px;line-height:1.33}
.code-space{position:absolute;left:91px;top:138px;width:126px;height:126px;background:var(--white);border:3px solid var(--gold-dark)}
</style>
</head>
<body>
<div class="label">
  <div class="gold-band top"></div>

  <section class="panel back">
    <div class="leaf-texture" role="img" aria-label="Faint tropical leaf pattern"></div>
    <div class="nutrition">
      <h3>Nutrition Facts</h3>
      <div>Serving Size 1 serving</div>
      <div class="rule-thick"></div>
      <div style="font-weight:700">Amount Per Serving</div>
      <div class="cal"><span>Calories</span><span>150</span></div>
      <div class="rule-mid"></div>
      <div class="row dv">%Daily Value*</div>
      <div class="row"><b>Total Fat</b> 13g</div>
      <div class="row indent">Saturated Fat 8g</div>
      <div class="row indent">Trans Fat 0g</div>
      <div class="row"><b>Cholesterol</b> 55mg</div>
      <div class="row"><b>Sodium</b> 5mg</div>
      <div class="row"><b>Total Carbohydrate</b> 10g</div>
      <div class="row indent">Dietary Fiber 0g</div>
      <div class="row indent">Total Sugars 9g</div>
      <div class="row indent">Includes Added Sugars 8g</div>
      <div class="row" style="border-bottom:2px solid var(--ink)"><b>Protein</b> 1g</div>
      <div class="row">• Vitamin D 10% DV &nbsp;• Calcium 2% DV</div>
      <div class="row">• Iron 0% DV • Potassium 1% DV</div>
      <p class="ingredients"><b>Ingredients</b>: Plumberry concentrate, Unsalted butter (cream, natural flavor), Cane sugar, Whole eggs, Egg yolks, Proprietary blend of natural flavors and spices.</p>
    </div>
    <p class="back-text" style="top:106px">Manufactured by<br>Keoni Bay Sweetworks, Hawai‘i.</p>
    <p class="back-text" style="top:168px">Keep Refrigerated.</p>
    <div class="barcode-space"></div>
  </section>

  <section class="panel front">
    <div class="brand-mark"></div>
    <h1 class="brand-name">Keoni Bay<br>Sweetworks</h1>
    <div class="est"><span class="line"></span>EST 1999<span class="line"></span></div>
    <h2 class="product-name">PLUMBERRY SPREAD</h2>
    <p class="front-foot net">Net Wt. 8 oz (227g)</p>
    <p class="front-foot origin">Made in Hawai‘i</p>
  </section>

  <section class="panel side">
    <div class="leaf-texture" role="img" aria-label="Faint tropical leaf pattern"></div>
    <p class="story">Keoni Bay Sweetworks brings authentic island flavors to every table. Our signature Plumberry Spread blends tropical fruit and fresh cream for a taste of pure aloha.</p>
    <div class="code-space"></div>
  </section>

  <div class="gold-band bottom"></div>
</div>
</body>
</html>
```